Property Developer Business card design

we need a business card design + printing for a new Property developer company based in melbourne.
We are a group of investors investing in a property developer business. We have more projects involved in residential property as opposed to commercial property but we are involved in both market. we also provide consulting services with overseas investors willing to invest in the australian property market.
Updates
I have uploaded the logo. I'm not very convince with the colors of my logo... any suggestion please?.
Thanks guys!
Target Market(s)
property investors or person willing to purchase investment property
Industry/Entity Type
Residential
Contact Information for Business Card
Bramblecourt Holdings Australia Pty Ltd
Look and feel

```html
<!DOCTYPE html>
<html lang="en">
<head>
<meta charset="utf-8">
<title>Bramblecourt Holdings Australia – Business Card</title>
<link rel="stylesheet" href="https://fonts.googleapis.com/css2?family=Arimo:wght@400;700&display=swap">
<style>
  :root {
    --page-bg: #dcdcdc;
    --brand-purple: #5c285c;
    --brand-green: #00874f;
    --card-white: #ffffff;
    --ink-light: #ffffff;
  }
  * { margin: 0; padding: 0; box-sizing: border-box; }
  html, body {
    width: 1200px; height: 985px; overflow: hidden;
    background: var(--page-bg);
    font-family: "Arimo", Arial, sans-serif;
  }
  .card {
    position: absolute;
    left: 290px;
    width: 620px; height: 354px;
    border-radius: 22px;
    overflow: hidden;
    box-shadow: 0 8px 18px rgba(0,0,0,0.18);
  }
  /* Back of card */
  .card-back {
    top: 90px;
    background: var(--brand-purple);
    color: var(--ink-light);
    display: flex; flex-direction: column;
    align-items: center; justify-content: center;
    gap: 22px;
  }
  .brand-mark {
    display: flex; align-items: center; gap: 14px;
  }
  .brand-mark .brand-square {
    width: 26px; height: 26px; background: currentColor;
  }
  .brand-mark .brand-name {
    font-weight: 700; font-size: 38px; line-height: 1;
  }
  .card-back .company-legal {
    font-size: 19px; letter-spacing: 0.3px;
  }
  /* Front of card */
  .card-front {
    top: 520px;
    background: var(--card-white);
  }
  .card-front .logo-panel {
    position: absolute; left: 0; top: 0;
    width: 290px; height: 100%;
    display: flex; align-items: center; justify-content: center;
    color: var(--brand-purple);
  }
  .card-front .logo-panel .brand-name {
    font-size: 30px; text-align: center; line-height: 1.15;
  }
  .card-front .divider {
    position: absolute; left: 296px; top: 0;
    width: 12px; height: 100%;
    background: var(--brand-purple);
  }
  .card-front .details-panel {
    position: absolute; left: 316px; top: 0; right: 0; bottom: 0;
    background: var(--brand-green);
    color: var(--ink-light);
    padding: 58px 24px 0 30px;
  }
  .person-name {
    font-weight: 700; font-size: 30px; letter-spacing: 1px;
  }
  .person-title {
    color: var(--brand-purple); font-size: 22px; margin-top: 2px;
  }
  .address {
    font-size: 18px; line-height: 1.2; margin-top: 18px;
  }
  .contact-list {
    list-style: none; font-size: 16px; line-height: 1.2; margin-top: 22px;
  }
  .contact-list .label { color: var(--brand-purple); }
</style>
</head>
<body>
  <section class="card card-back" aria-label="Card back">
    <div class="brand-mark">
      <span class="brand-square" aria-hidden="true"></span>
      <span class="brand-name">Bramblecourt Holdings</span>
    </div>
    <p class="company-legal">Bramblecourt Holdings Australia Pty Ltd</p>
  </section>

  <section class="card card-front" aria-label="Card front">
    <div class="logo-panel">
      <div class="brand-mark">
        <span class="brand-name">Bramblecourt<br>Holdings</span>
      </div>
    </div>
    <div class="divider" aria-hidden="true"></div>
    <div class="details-panel">
      <h1 class="person-name">Jordan Hale</h1>
      <p class="person-title">Managing Director</p>
      <p class="address">14 Wattlebird Lane<br>Greenvale VIC 3059</p>
      <ul class="contact-list">
        <li><span class="label">T:</span> +61 3 9000 1234</li>
        <li><span class="label">M:</span> 0400 555 018</li>
        <li><span class="label">E:</span> jordan.hale@bramblecourt.com.au</li>
      </ul>
    </div>
  </section>
</body>
</html>
```